Storm Restoration Contractor needs a professional letterhead design

Looking for a professional letterhead design. Not looking for your cheapo MS Word standard ones that are readily available. Dont want it to be cookie cutter look like ones readily available online. We just recently changed our logo and want to freshen up all our documents. Our company handles restoring a property back to a pre-loss condition after a storm damages it. For example, wind, hail, flood, fire losses.

Target Market(s)

Property Owners, Homeowners, Property Owners, Commercial Property Owners, Property Management Companies

Industry/Entity Type

Construction Company

Requirements
Must have
• Professional, Use 1 of 2 logo options
• Storm Restoration, Roofing, Siding, Windows

```html
<!DOCTYPE html>
<html lang="en">
<head>
<meta charset="utf-8">
<title>Restora Shell – Letterhead</title>
<link href="https://fonts.googleapis.com/css2?family=Open+Sans:wght@400;600&display=swap" rel="stylesheet">
<style>
  :root {
    --backdrop: #e4e4e4;
    --paper: #ffffff;
    --brand-blue: #1a73c4;
    --brand-gray: #5a5a5c;
    --ink: #3a3a3a;
    --rule: #9a9a9a;
    --mark-tint: #e6eff8;
  }
  * { margin: 0; padding: 0; box-sizing: border-box; }
  html, body { width: 1200px; height: 1200px; overflow: hidden; }
  body {
    background: var(--backdrop);
    font-family: "Open Sans", Arial, sans-serif;
    display: flex; align-items: center; justify-content: center;
  }
  .letterhead {
    position: relative;
    width: 778px; height: 1100px;
    background: var(--paper);
    box-shadow: 0 6px 24px rgba(0,0,0,.12);
    overflow: hidden;
  }
  .brand {
    position: absolute; top: 70px; left: 64px;
    display: flex; align-items: center; gap: 12px;
  }
  .brand-dot {
    width: 34px; height: 34px; border-radius: 50%;
    background: var(--brand-blue);
  }
  .brand-name {
    color: var(--brand-blue);
    font-weight: 600; font-size: 22px;
    letter-spacing: 3px; text-transform: uppercase;
    white-space: nowrap;
  }
  .backdrop-ring {
    position: absolute; left: 50%; top: 50%;
    width: 400px; height: 400px;
    transform: translate(-50%, -50%);
    border-radius: 50%;
    border: 30px solid var(--mark-tint);
  }
  .contact {
    position: absolute; right: 56px; bottom: 56px;
    text-align: right;
    color: var(--ink); font-size: 12px; line-height: 1.45;
    white-space: nowrap;
  }
  .contact-address { padding-bottom: 8px; }
  .contact-rule { border: 0; border-top: 1px solid var(--rule); margin-bottom: 7px; }
  .contact-lines {
    display: flex; justify-content: flex-end; gap: 14px; align-items: center;
  }
  .contact-item { display: inline-flex; align-items: center; gap: 5px; white-space: nowrap; }
  .contact-item svg { width: 10px; height: 10px; flex: 0 0 10px; fill: var(--brand-blue); }
  .footer-band {
    position: absolute; left: 0; right: 0; bottom: 0; height: 12px;
    display: flex;
  }
  .footer-band-blue { flex: 0 0 70%; background: var(--brand-blue); }
  .footer-band-gray { flex: 1; background: var(--brand-gray); }
</style>
</head>
<body>
  <main class="letterhead">
    <header class="brand">
      <span class="brand-dot"></span>
      <span class="brand-name">Restora Shell</span>
    </header>

    <div class="backdrop-ring" aria-hidden="true"></div>

    <footer class="contact">
      <p class="contact-address">512 W. Harbor Rd Ste 210<br>Lakemont, OH 44102</p>
      <hr class="contact-rule">
      <p class="contact-lines">
        <span class="contact-item">
          <svg viewBox="0 0 10 10" aria-hidden="true"><path d="M2 0.5 L3.8 2.6 L2.8 3.8 Q4 6 6.2 7.2 L7.4 6.2 L9.5 8 L8.3 9.5 Q1 8 0.5 1.7 Z"/></svg>
          555-014-2290
        </span>
        <span class="contact-item">
          <svg viewBox="0 0 10 10" aria-hidden="true"><rect x="2.5" y="0.5" width="5" height="3"/><rect x="0.5" y="3.5" width="9" height="4.5" rx="1"/><rect x="2.5" y="7" width="5" height="2.5"/></svg>
          555-014-7731
        </span>
        <span class="contact-item">
          <svg viewBox="0 0 10 10" aria-hidden="true"><circle cx="5" cy="5" r="4.5"/></svg>
          www.restorashell.com
        </span>
      </p>
    </footer>

    <div class="footer-band" aria-hidden="true">
      <span class="footer-band-blue"></span>
      <span class="footer-band-gray"></span>
    </div>
  </main>
</body>
</html>
```